Vegan Alfredo Sauce Label Design for Bramble Kitchen Co

We are a food co. committed to making vegan food more accessible to people who want to eat healthier. Our first line of product is vegan Alfredo sauce.
We have 3 flavors:
- Garlic
- Pesto
- Lemony Artichoke
The current project is the design for the first flavor: garlic. However, we would like a template that would translate well to other flavors, so they look like a family of products.
These will be in standard 16 oz jars. The whole label will be approx 6cm x 24cm, but the front visual space is approx 6cm x 10cm. The rest will be nutritional labeling and copy about the company.
We also need a stamp or font- based logo that says Bramble Kitchen Co. (or lower case: bramble kitchen co.), the name of the company.
The picture (attached) of Vegan Queso is the closest to what we are going for. Because the sauce is creamy white, a colorful background with off-white font will be best.
We currently have a website, although we are doing a brand over-haul (hence, this posting) www.bramblekitchenco.example. If the designer is a good fit, we have several more projects, in line.
Other brands we love: Tidy Larder, Marlow Ridge Pantry, Pulp Poured Daily.
The final brand should communicate hip, natural and health.
And personally, I love design that is clever and somehow makes me smile.
Target Market(s)
Vegans, vegetarians, and people with common food allergies - all ages.
Young, hip families.
Industry/Entity Type
It Company
Requirements
Must have
- Copy:
Vegan Alfredo or Vegan Alfredo Sauce
Garlic
Bramble Kitchen or Bramble Kitchen Co
16 oz
Nice to have
- May include copy:
Gluten-Free Soy-Free Nut-Free
Should not have
- Neon colors

```html
<!DOCTYPE html>
<html lang="en">
<head>
<meta charset="utf-8">
<title>Bramble Kitchen Co — Vegan Alfredo Sauce Labels, Option 1</title>
<link href="https://fonts.googleapis.com/css2?family=Cinzel:wght@400&family=Open+Sans:wght@600;700&family=Roboto+Condensed:wght@400&display=swap" rel="stylesheet">
<style>
  :root {
    --page: #ffffff;
    --ink: #1c1c1c;
    --cream: #fbf3dc;
    --white: #ffffff;
    --sub: #5a4b5e;
    --yellow-a: #d8bc00;
    --yellow-b: #e0c632;
    --pink-a: #c88b87;
    --pink-b: #d5a29e;
    --green-a: #7c9d22;
    --green-b: #9bb253;
  }
  * { margin: 0; padding: 0; box-sizing: border-box; }
  html, body { width: 1200px; height: 900px; overflow: hidden; background: var(--page); }
  .canvas { position: relative; width: 1200px; height: 900px; }

  .option-title {
    position: absolute; left: 35px; top: 24px;
    font-family: "Cinzel", serif; font-size: 22px; letter-spacing: 5px;
    color: var(--ink);
  }

  .label {
    position: absolute; left: 118px; width: 963px; height: 234px;
    --a: #000; --b: #111;
    background: repeating-linear-gradient(90deg, var(--a) 0 16.5px, var(--b) 16.5px 33px);
  }
  .label--artichoke { top: 75px; --a: var(--yellow-a); --b: var(--yellow-b); }
  .label--garlic { top: 332px; --a: var(--pink-a); --b: var(--pink-b); }
  .label--pesto { top: 590px; --a: var(--green-a); --b: var(--green-b); }

  .label > * { position: absolute; left: 50%; transform: translate(-50%, -50%); white-space: nowrap; }

  .brand-mark {
    width: 11px; height: 11px; border-radius: 50%; background: var(--white);
  }
  .brand-name {
    font-family: "Open Sans", sans-serif; font-weight: 700; font-size: 14px;
    color: var(--white); letter-spacing: 0.2px;
  }
  .flavor-art { border-radius: 40px; }
  .flavor-art--artichoke {
    width: 96px; height: 78px;
    background: radial-gradient(circle at 50% 30%, #f0d24a 0 14%, #7c8a3c 30%, #5f7230 70%, transparent 72%);
  }
  .flavor-art--garlic {
    width: 82px; height: 80px;
    background: radial-gradient(circle at 50% 50%, #d9b9a6 0 30%, #b98d78 55%, transparent 70%);
  }
  .flavor-art--pesto {
    width: 84px; height: 56px;
    background: radial-gradient(ellipse at 50% 55%, #4d7a2c 0 35%, #3d6424 60%, transparent 72%);
  }

  .flavor-kicker {
    font-family: "Cinzel", serif; font-size: 13px; letter-spacing: 4px; color: var(--cream);
  }
  .flavor-name {
    font-family: "Cinzel", serif; font-size: 38px; letter-spacing: 4px; color: var(--cream);
    line-height: 1;
  }
  .product-type {
    font-family: "Open Sans", sans-serif; font-weight: 700; font-size: 9.5px;
    letter-spacing: 0.8px; color: var(--sub);
  }
  .claims {
    font-family: "Roboto Condensed", sans-serif; font-size: 10.5px; letter-spacing: 0.8px;
    color: var(--white);
  }
  .claims .size { font-size: 13px; letter-spacing: 0; margin-left: 3px; }
</style>
</head>
<body>
<main class="canvas">
  <h1 class="option-title">OPTION 1</h1>

  <section class="label label--artichoke">
    <span class="brand-mark" style="top:18px"></span>
    <span class="brand-name" style="top:34px">bramblekitchenco</span>
    <div class="flavor-art flavor-art--artichoke" style="top:86px" role="img" aria-label="Illustration of four artichokes around a lemon slice"></div>
    <p class="flavor-kicker" style="top:142px">LEMONY</p>
    <h2 class="flavor-name" style="top:168px">ARTICHOKE</h2>
    <p class="product-type" style="top:193px">VEGAN ALFREDO SAUCE</p>
    <p class="claims" style="top:214px">GLUTEN-FREE • SOY-FREE • NUT-FREE <span class="size">16oz</span></p>
  </section>

  <section class="label label--garlic">
    <span class="brand-mark" style="top:19px"></span>
    <span class="brand-name" style="top:36px">bramblekitchenco</span>
    <div class="flavor-art flavor-art--garlic" style="top:93px" role="img" aria-label="Illustration of garlic cloves arranged like a flower"></div>
    <h2 class="flavor-name" style="top:158px">GARLIC</h2>
    <p class="product-type" style="top:185px">VEGAN ALFREDO SAUCE</p>
    <p class="claims" style="top:214px">GLUTEN-FREE • SOY-FREE • NUT-FREE <span class="size">16oz</span></p>
  </section>

  <section class="label label--pesto">
    <span class="brand-mark" style="top:17px"></span>
    <span class="brand-name" style="top:34px">bramblekitchenco</span>
    <div class="flavor-art flavor-art--pesto" style="top:80px" role="img" aria-label="Illustration of basil leaves with a garlic clove"></div>
    <h2 class="flavor-name" style="top:155px">PESTO</h2>
    <p class="product-type" style="top:185px">VEGAN ALFREDO SAUCE</p>
    <p class="claims" style="top:214px">GLUTEN-FREE • SOY-FREE • NUT-FREE <span class="size">16oz</span></p>
  </section>
</main>
</body>
</html>
```